New website for out outstanding veterinary training center

We already have a beautiful logo with nice colors and we are now looking for a breathtaking modern website to present our training center and future corses held there. A section to book open courses should also be available.

We are planing the realize the website with Wordpress.
The following pages should be available:
- Startpage / Overview
- Page to present the different rooms and seating option
- Page where the rooms can be booked
- Page where recommended accommodation are presented
- Page to present and book corses
- contact page
- Impressum

Target Market(s)

European Union

Industry/Entity Type

Education, Veterinary medicine

Number of Pages Required

5+ page

Font styles to use
Sans Serif

Colors
00AB8E
00BBA5
67D7C9
C6EFE9
E9F9F6

Requirements
Must have
• The website must be clear and easy to read. The colors form the logos should be used for the design.
Should not have
• To playful design. The page is not for a veterinary practice. we are a training center for veterinarians!

```html
<!DOCTYPE html>
<html lang="en">
<head>
<meta charset="utf-8">
<title>Veterra Training Center</title>
<link href="https://fonts.googleapis.com/css2?family=Montserrat:wght@600;700&family=Roboto:wght@400;500;700&display=swap" rel="stylesheet">
<style>
:root{
  --teal:#1f928a;
  --teal-dark:#17807a;
  --ink:#4b4b4d;
  --text:#6b6b6b;
  --grey-bg:#f3f3f3;
  --white:#ffffff;
  --dark:#2b2f31;
}
*{margin:0;padding:0;box-sizing:border-box}
html,body{width:1200px;height:3568px;overflow:hidden}
body{position:relative;font-family:Roboto,Arial,sans-serif;color:var(--text);background:var(--white)}
.abs{position:absolute}
.btn{position:absolute;display:flex;align-items:center;justify-content:center;background:var(--teal);color:#fff;font-weight:700;font-size:15px;border-radius:30px;text-transform:uppercase}
h1,h2,h3{font-family:Montserrat,Arial,sans-serif;font-weight:700}
.topline{top:0;left:0;width:1200px;height:4px;background:var(--teal)}
.header{top:4px;left:0;width:1200px;height:92px;background:#fff;z-index:2}
.logo-badge{left:70px;top:-60px;width:220px;height:225px;border-radius:50%;background:#fff;z-index:3;display:flex;flex-direction:column;align-items:center;justify-content:flex-end;padding-bottom:58px}
.logo-dot{width:60px;height:60px;border-radius:50%;background:var(--teal);margin-bottom:8px}
.logo-name{font-family:Roboto,sans-serif;font-weight:700;font-size:24px;color:var(--teal)}
.nav{top:42px;left:344px;display:flex;gap:22px;font-size:14px;font-weight:500;color:#333;z-index:3}
.nav .active{color:var(--teal)}
.hero-photo{top:96px;left:0;width:1200px;height:670px;background:linear-gradient(90deg,#e9ece8 0%,#dfe3df 40%,#eef0ef 60%,#c9d6cf 100%)}
.hero-title{top:318px;left:111px;font-size:33px;color:var(--ink);letter-spacing:.3px}
.hero-title span,.accent{color:var(--teal)}
.hero-text{top:370px;left:140px;width:510px;text-align:center;font-size:18px;font-weight:500;color:#333;line-height:28px}
.section-title{width:1200px;left:0;text-align:center;color:var(--ink)}
.welcome-text{top:858px;left:140px;width:920px;text-align:center;font-size:14px;line-height:26px}
.courses-bg{top:1105px;left:0;width:1200px;height:580px;background:var(--grey-bg)}
.card{background:#fff;box-shadow:0 2px 6px rgba(0,0,0,.12);width:476px;height:178px;display:flex;padding:8px}
.card .pic{width:145px;height:162px;flex:none}
.card .body{padding:10px 18px 0 20px}
.card h3{font-family:Roboto,sans-serif;font-weight:500;font-size:18px;color:#333;margin-bottom:12px}
.card p{font-size:14px;line-height:24px;text-align:justify}
.more{display:block;color:var(--teal);font-weight:500;font-size:14px;margin-top:8px;text-transform:uppercase}
.more svg{vertical-align:-2px;margin-left:8px}
.why{top:1685px;left:0;width:1200px;height:507px;background:linear-gradient(90deg,#2b958d,#3a9e96 50%,#2b958d)}
.feature{width:320px;text-align:center;color:#fff}
.feature .circle{width:102px;height:102px;border-radius:50%;background:#fff;margin:0 auto 38px;display:flex;align-items:center;justify-content:center}
.feature h3{font-size:20px;margin-bottom:18px}
.feature p{font-size:14px;line-height:22px}
.post{width:314px}
.post .pic{height:222px}
.post .box{margin:-60px 15px 0;height:232px;background:#fff;box-shadow:0 2px 6px rgba(0,0,0,.12);position:relative;border-radius:140px 140px 0 0/30px 30px 0 0;text-align:center;padding-top:52px}
.post .date{font-size:14px;color:#555}
.post h3{font-family:Roboto,sans-serif;font-weight:500;font-size:21px;color:#333;margin:10px 0 12px}
.post p{font-size:14px;line-height:22px;padding:0 8px}
.post .more{margin-top:10px}
.cta{top:2846px;left:111px;width:978px;height:420px;background:linear-gradient(135deg,#3a3f41,#24282a)}
.cta-text{top:2960px;left:111px;width:978px;text-align:center;color:#fff;font-size:15px;font-weight:500;line-height:26px}
.foot-logo{top:3298px;left:111px;width:170px;display:flex;flex-direction:column;align-items:center}
.foot-logo .logo-dot{width:100px;height:100px}
.foot-col h4{font-size:19px;font-weight:500;color:#333;margin-bottom:18px}
.foot-col li{list-style:none;font-size:15px;color:#444;height:24px;display:flex;align-items:center;gap:22px}
.copy{top:3524px;left:111px;font-size:12px;color:#555}
.copy b{color:#333}
.social{top:3508px;left:924px;display:flex;gap:9px}
.social span{width:34px;height:34px;border-radius:50%;border:1px solid #ccc}
.social span.on{background:var(--teal);border-color:var(--teal)}
</style>
</head>
<body>
<div class="abs topline"></div>
<header class="abs header">
  <nav class="abs nav">
    <span class="active">HOME</span><span>ABOUT US</span><span>WHERE THE ROOMS</span><span>ACCOMODATION</span><span>CONTACT</span>
  </nav>
  <div class="btn" style="left:888px;top:21px;width:200px;height:52px;font-size:14px">Book open courses</div>
</header>
<div class="abs logo-badge"><div class="logo-dot"></div><div class="logo-name">Veterra</div></div>

<div class="abs hero-photo" role="img" aria-label="Veterinarian examining a young labrador with a stethoscope in a bright clinic"></div>
<svg class="abs" style="top:640px;left:0" width="1200" height="130" viewBox="0 0 1200 130">
  <path d="M0 126 Q600 -70 1200 126 L1200 130 L0 130Z" fill="var(--teal)"/>
  <path d="M0 130 Q600 -50 1200 130Z" fill="#fff"/>
</svg>
<h1 class="abs hero-title">VETERRA <span>TRAINING CENTER</span></h1>
<p class="abs hero-text">Lorem ipsum dolor sit amet, consectetur adipis ing elit sed do eiusum amet consemod tema.</p>
<div class="btn" style="left:313px;top:444px;width:157px;height:47px">Get started</div>

<h2 class="abs section-title" style="top:766px;font-size:28px;line-height:36px">WELCOME TO<br><span class="accent">VETERRA TRAINING CENTER</span></h2>
<p class="abs welcome-text">Lorem ipsum dolor sit amet, consectetur adipiscing elit, sed do eiusmod tempor incididunt ut labore et dolore magna aliqua. Ut enim ad minim veniam, quis nostrud exercitation ullamco laboris nisi ut aliquip ex ea commodo consequat. Duis aute irure dolor in reprehenderit in voluptate velit esse cillum dolore eu fugiat nulla pariatur. Excepteur sint occaecat cupidatat non proident.</p>
<div class="btn" style="left:522px;top:962px;width:156px;height:48px">Learn more</div>

<div class="abs courses-bg"></div>
<h2 class="abs section-title" style="top:1162px;font-size:34px">OUR <span class="accent">COURSES</span></h2>
<div class="abs card" style="left:111px;top:1243px"><div class="pic" role="img" aria-label="Vet nurse grooming a golden retriever" style="background:linear-gradient(#e8ebe9,#c9d3d8)"></div><div class="body"><h3>Ut enim ad minim veniam, quisa</h3><p>Lorem ipsum dolor sit amet, consectetur adipi scing elit, sed do eiusmod tempor incid idunt labore et dolore maga.</p><span class="more">Book now<svg width="13" height="13" viewBox="0 0 13 13"><circle cx="6.5" cy="6.5" r="6.5" fill="var(--teal)"/><path d="M4 6.5h5M7 4l2.5 2.5L7 9" stroke="#fff" stroke-width="1.6" fill="none"/></svg></span></div></div>
<div class="abs card" style="left:613px;top:1243px"><div class="pic" role="img" aria-label="Smiling vet holding a cat" style="background:linear-gradient(#eef0ef,#cfd5d6)"></div><div class="body"><h3>Ut enim ad minim veniam, quisa</h3><p>Lorem ipsum dolor sit amet, consectetur adipi scing elit, sed do eiusmod tempor incid idunt labore et dolore maga.</p><span class="more">Book now<svg width="13" height="13" viewBox="0 0 13 13"><circle cx="6.5" cy="6.5" r="6.5" fill="var(--teal)"/><path d="M4 6.5h5M7 4l2.5 2.5L7 9" stroke="#fff" stroke-width="1.6" fill="none"/></svg></span></div></div>
<div class="abs card" style="left:111px;top:1443px"><div class="pic" role="img" aria-label="Vet in blue scrubs holding a ginger cat" style="background:linear-gradient(#f1f1ef,#b8cde0)"></div><div class="body"><h3>Ut enim ad minim veniam, quisa</h3><p>Lorem ipsum dolor sit amet, consectetur adipi scing elit, sed do eiusmod tempor incid idunt labore et dolore maga.</p><span class="more">Book now<svg width="13" height="13" viewBox="0 0 13 13"><circle cx="6.5" cy="6.5" r="6.5" fill="var(--teal)"/><path d="M4 6.5h5M7 4l2.5 2.5L7 9" stroke="#fff" stroke-width="1.6" fill="none"/></svg></span></div></div>
<div class="abs card" style="left:613px;top:1443px"><div class="pic" role="img" aria-label="Two vets holding a beagle" style="background:linear-gradient(#e6ecef,#9fbbd3)"></div><div class="body"><h3>Ut enim ad minim veniam, quisa</h3><p>Lorem ipsum dolor sit amet, consectetur adipi scing elit, sed do eiusmod tempor incid idunt labore et dolore maga.</p><span class="more">Book now<svg width="13" height="13" viewBox="0 0 13 13"><circle cx="6.5" cy="6.5" r="6.5" fill="var(--teal)"/><path d="M4 6.5h5M7 4l2.5 2.5L7 9" stroke="#fff" stroke-width="1.6" fill="none"/></svg></span></div></div>

<section class="abs why" role="img" aria-label="Teal tinted background of a vet with a pet"></section>
<h2 class="abs section-title" style="top:1750px;font-size:34px;color:#fff">WHY CHOOSE US</h2>
<div class="abs feature" style="left:103px;top:1849px"><div class="circle"><svg width="50" height="50" viewBox="0 0 50 50" fill="none" stroke="#555" stroke-width="2"><circle cx="25" cy="16" r="4"/><circle cx="17" cy="10" r="2.5"/><circle cx="25" cy="7" r="2.5"/><circle cx="33" cy="10" r="2.5"/><path d="M6 22v12l10 10M44 22v12L34 44M12 30l8 8M38 30l-8 8"/></svg></div><h3>LOREM IPSUM DOL</h3><p>Lorem ipsum dolor sit amet, consectetur adi piscing elit, sed do eiusmod tempor incididunt ut labore et doloing elit, sed do eiusmod tempor inre magna aliqua.</p></div>
<div class="abs feature" style="left:440px;top:1849px"><div class="circle"><svg width="56" height="50" viewBox="0 0 56 50" fill="none" stroke="#555" stroke-width="2"><path d="M28 44 8 24A11 11 0 0 1 28 10 11 11 0 0 1 48 24Z"/><path d="M2 26h16l4-7 5 13 4-9 3 3h20"/></svg></div><h3>LOREM IPSUM DOL</h3><p>Lorem ipsum dolor sit amet, consectetur adi piscing elit, sed do eiusmod tempor incididunt ut labore et doloing elit, sed do eiusmod tempor inre magna aliqua.</p></div>
<div class="abs feature" style="left:777px;top:1849px"><div class="circle"><svg width="50" height="50" viewBox="0 0 50 50" fill="none" stroke="#555" stroke-width="2"><path d="M10 44V28l4-10 4 4h6l2-8 4 6v24M26 44V32c6-4 12 0 12 6v6M38 44h6"/></svg></div><h3>LOREM IPSUM DOL</h3><p>Lorem ipsum dolor sit amet, consectetur adi piscing elit, sed do eiusmod tempor incididunt ut labore et doloing elit, sed do eiusmod tempor inre magna aliqua.</p></div>

<h2 class="abs section-title" style="top:2280px;font-size:34px">LATEST BLOG POST</h2>
<article class="abs post" style="left:111px;top:2356px"><div class="pic" role="img" aria-label="Vet listening to a cat's heartbeat" style="background:linear-gradient(#e9ecea,#c3c9cc)"></div><div class="box"><div class="date">▦ 17 Oct 2021</div><h3>Lorem ipsum dolor sita</h3><p>Sed ut perspiciatis unde omnis iste natus error sit voluptatem accusantium do loremque laudantiuma.</p><span class="more">Read more<svg width="13" height="13" viewBox="0 0 13 13"><circle cx="6.5" cy="6.5" r="6.5" fill="var(--teal)"/><path d="M4 6.5h5M7 4l2.5 2.5L7 9" stroke="#fff" stroke-width="1.6" fill="none"/></svg></span></div></article>
<article class="abs post" style="left:443px;top:2356px"><div class="pic" role="img" aria-label="Two vets treating a beagle on an exam table" style="background:linear-gradient(#dfe8ea,#9cb6c2)"></div><div class="box"><div class="date">▦ 17 Oct 2021</div><h3>Lorem ipsum dolor sita</h3><p>Sed ut perspiciatis unde omnis iste natus error sit voluptatem accusantium do loremque laudantiuma.</p><span class="more">Read more<svg width="13" height="13" viewBox="0 0 13 13"><circle cx="6.5" cy="6.5" r="6.5" fill="var(--teal)"/><path d="M4 6.5h5M7 4l2.5 2.5L7 9" stroke="#fff" stroke-width="1.6" fill="none"/></svg></span></div></article>
<article class="abs post" style="left:775px;top:2356px"><div class="pic" role="img" aria-label="Vet examining a tabby cat" style="background:linear-gradient(#eef0f0,#9fb4c8)"></div><div class="box"><div class="date">▦ 17 Oct 2021</div><h3>Lorem ipsum dolor sita</h3><p>Sed ut perspiciatis unde omnis iste natus error sit voluptatem accusantium do loremque laudantiuma.</p><span class="more">Read more<svg width="13" height="13" viewBox="0 0 13 13"><circle cx="6.5" cy="6.5" r="6.5" fill="var(--teal)"/><path d="M4 6.5h5M7 4l2.5 2.5L7 9" stroke="#fff" stroke-width="1.6" fill="none"/></svg></span></div></article>

<section class="abs cta" role="img" aria-label="Dark photo of a woman with her dog"></section>
<h2 class="abs section-title" style="top:2893px;font-size:32px;color:#fff">GET READY TO START?</h2>
<p class="abs cta-text">Lorem ipsum dolor sit amet, consectetur adipiscing elit, sed do eiusmod tempor incididunt ut labore et dolore magna aliqua.<br>Ut enim ad minim veniam, quis nostrud exercitation ullamco laboris nisi ut aliquip</p>
<div class="btn" style="left:522px;top:3035px;width:156px;height:50px">Contact us</div>

<svg class="abs" style="top:3120px;left:0" width="1200" height="200" viewBox="0 0 1200 200">
  <path d="M0 196 Q600 -80 1200 196 L1200 200 L0 200Z" fill="var(--teal)"/>
  <path d="M0 200 Q600 -60 1200 200Z" fill="#fff"/>
</svg>
<div class="abs foot-logo"><div class="logo-dot"></div><div class="logo-name" style="font-size:30px">Veterra</div></div>
<div class="abs foot-col" style="left:355px;top:3290px"><h4>Quick Links</h4><ul><li>➜ Home</li><li>➜ About Us</li><li>➜ Where The Rooms</li><li>➜ Accomodation</li><li>➜ Contact</li></ul></div>
<div class="abs foot-col" style="left:626px;top:3290px"><h4>About</h4><ul><li>➜ Site Map</li><li>➜ Priacy Policy</li><li>➜ Term &amp; Conditions</li><li>➜ Impressum</li></ul></div>
<div class="abs foot-col" style="left:890px;top:3290px"><h4>Contact Us</h4>
  <ul>
    <li style="align-items:flex-start;height:52px"><svg width="12" height="16" viewBox="0 0 12 16"><path d="M6 0a6 6 0 0 1 6 6c0 4-6 10-6 10S0 10 0 6a6 6 0 0 1 6-6z" fill="var(--teal)"/><circle cx="6" cy="6" r="2" fill="#fff"/></svg><span>18 Linden Avenue<br>Springfield</span></li>
    <li style="height:30px"><svg width="14" height="14" viewBox="0 0 14 14"><path d="M3 0l3 4-2 2c1 2 2 3 4 4l2-2 4 3-2 3C6 14 0 8 0 2z" fill="var(--teal)"/></svg><span>555-014-2290</span></li>
    <li><svg width="15" height="12" viewBox="0 0 15 12" fill="none" stroke="var(--teal)" stroke-width="1.4"><rect x="1" y="1" width="13" height="10"/><path d="M1 1l6.5 6L14 1"/></svg><span>info@veterra-academy.com</span></li>
  </ul>
</div>
<div class="abs" style="top:3508px;left:111px;width:978px;height:1px;background:#e5e5e5"></div>
<p class="abs copy">© 2021 <b>Veterra <span class="accent">TRAINING CENTER</span></b>. All rights reserved</p>
<div class="abs social" style="top:3517px"><span class="on"></span><span></span><span></span><span></span></div>
</body>
</html>
```